Build a landing page to promote a service (dialler consultation and support).

We are a call centre consultation firm and we need a landing page to promote a service. The service is Tormalux dialler consultation and support.
If you do not know what Tormalux is, please do some quick "Zorvex" research for more information.
The landing page will be promoted with a paid advertisement, so we want something that is simple, and explains exactly what service we offer.
There are two objectives for the landing page:
1) A "call to action" which directs the user to a contact page, including a form plus all of our contact details.
2) A form for them viewers to enter their details to get a "FREE" quote for their project. This form should be placed on the main page.
Notes:
The call to action will require the viewer to enter their name, email, phone number as well as a description of their request. There will also need to be a drop down menu for the type of quote. This menu should have the following options:
1) Tormalux support
2) Tormalux hosting
3) Tormalux customisation
4) Other
We need 2 pages in total:
1) Main landing page
This is the home page. It will need to clearly indicate our services and our key selling features.
Services:
* Tormalux support
* Tormalux hosting
* Tormalux customisation
Key Selling Features:
* Australian based
* PCI complaint
* 10+ years of dialler and call centre experience
* we run a sister company which is a highly reputable 40 seat call centre, so we know first hand about call centre technology.
The main landing page will have an "about us" section with a few paragraphs about how we got started.
-------------------------------------------------------------------------
2) Contact page
All of our contact details will live on this page, as well as a contact form.
Other notes:
We will be self hosting the landing page.
We already have a domain name.
The design must be clean and incorporate our logo, as well as it's colours. (Logo attached)
We want a fully function HTML landing page, not just a "PSD" design.
The page must be mobile optimised.
Anyone using Tormalux software.

```html
<!DOCTYPE html>
<html lang="en">
<head>
<meta charset="utf-8">
<title>Callwise – Tormalux Dialler Consultation</title>
<link href="https://fonts.googleapis.com/css2?family=Poppins:wght@400;500;600;700&display=swap" rel="stylesheet">
<style>
:root{
  --stage:#3dbfa4;
  --blue:#1a78c8;
  --blue-dark:#1566ad;
  --teal:#2fb59a;
  --ink:#222;
  --muted:#555;
  --line:#dfe3e6;
  --soft:#f1f2f3;
  --white:#fff;
}
*{box-sizing:border-box;margin:0;padding:0}
html,body{width:931px;height:1200px;overflow:hidden}
body{background:var(--stage);font-family:"Poppins",sans-serif;color:var(--ink);position:relative}
.page{position:absolute;top:140px;width:434px;background:var(--white);overflow:hidden}
.page--home{left:22px;height:918px}
.page--contact{left:475px;height:651px}

/* header */
.site-header{position:absolute;left:0;top:0;width:434px;height:53px;background:var(--white)}
.brand{position:absolute;left:34px;top:3px;width:80px;text-align:center}
.brand__dot{display:block;width:30px;height:30px;border-radius:50%;background:var(--blue);margin:0 auto 1px}
.brand__name{font-size:12px;font-weight:500;color:var(--blue);letter-spacing:.5px;line-height:14px}
.contact-strip{position:absolute;top:13px;left:132px;display:flex;gap:14px;font-size:5.6px;color:var(--ink);white-space:nowrap}
.contact-strip span{display:flex;align-items:center;gap:3px}
.contact-strip svg{width:6px;height:6px;fill:var(--ink)}
.main-nav{position:absolute;top:32px;right:30px;display:flex;align-items:center;gap:9px;font-size:6px;color:var(--ink)}
.main-nav .is-active{color:var(--blue);font-weight:600}
.social-mini{display:flex;gap:4px;align-items:center}
.social-mini i{display:block;width:4.5px;height:4.5px;border-radius:50%;background:var(--ink)}
.main-nav svg{width:6px;height:6px}

/* hero */
.hero{position:absolute;left:0;top:53px;width:434px;overflow:hidden}
.hero__photo{position:absolute;inset:0;
  background:
    radial-gradient(ellipse 60px 90px at 28% 45%,rgba(214,170,140,.55),transparent 70%),
    radial-gradient(ellipse 90px 120px at 25% 85%,rgba(205,195,185,.9),transparent 70%),
    radial-gradient(ellipse 50px 40px at 26% 12%,rgba(180,140,95,.7),transparent 70%),
    radial-gradient(ellipse 70px 60px at 92% 55%,rgba(25,28,34,.85),transparent 70%),
    radial-gradient(ellipse 60px 50px at 70% 70%,rgba(40,44,52,.7),transparent 70%),
    radial-gradient(ellipse 120px 50px at 60% 10%,rgba(235,232,225,.8),transparent 70%),
    linear-gradient(100deg,#8a7c6e 0%,#c9bcae 18%,#a59d95 40%,#6f737a 62%,#9aa0a8 80%,#3e4249 100%)}
.hero__photo--dim::after{content:"";position:absolute;inset:0;background:rgba(20,25,35,.25)}
.hero__curve{position:absolute;left:0;bottom:0;width:434px;height:40px}
.quote-box{position:absolute;left:218px;top:25px;width:174px;height:156px;background:rgba(255,255,255,.93);padding:5px 14px 0}
.quote-box h2{font-size:10.5px;font-weight:700;color:var(--blue);text-align:center;line-height:12px}
.quote-box p{font-size:4.8px;color:var(--muted);text-align:center;line-height:7px;margin-bottom:3px}
.field{display:block;height:11px;border:1px solid var(--line);background:var(--white);font-size:4.6px;color:#777;padding:2px 6px;margin-bottom:4.5px;line-height:6px}
.field-row{display:flex;gap:3px}
.field-row .field{flex:1}
.field--select{position:relative}
.field--select::after{content:"";position:absolute;right:5px;top:4px;border:2px solid transparent;border-top-color:#555}
.field--area{height:26px}
.btn-quote{display:block;height:15px;background:var(--blue);color:var(--white);font-size:5.6px;text-align:center;line-height:15px;font-weight:500}

/* section titles */
.sec-title{position:absolute;left:0;width:434px;text-align:center;font-size:11px;font-weight:700;color:var(--blue-dark);text-transform:uppercase}
.sec-lead{position:absolute;left:62px;width:310px;text-align:center;font-size:5.4px;line-height:9.5px;color:var(--ink)}

/* services */
.service{position:absolute;top:350px;width:112px;height:81px;border:1px solid #eceeef;text-align:center;padding-top:7px;background:var(--white)}
.service svg{display:block;width:18px;height:18px;margin:0 auto;stroke:var(--teal);fill:none;stroke-width:1.3}
.service h3{font-size:7.2px;font-weight:600;color:var(--teal);margin:5px 0 2px;line-height:10px}
.service p{font-size:4.9px;line-height:8px;color:var(--ink);padding:0 14px}
.service--featured{background:var(--teal);border-color:var(--teal)}
.service--featured svg{stroke:var(--white)}
.service--featured h3,.service--featured p{color:var(--white)}

/* about */
.about{position:absolute;left:0;top:446px;width:434px;height:157px;
  background:radial-gradient(ellipse 160px 90px at 80% 40%,rgba(70,80,95,.6),transparent 70%),linear-gradient(90deg,#23272c,#343a41 60%,#262a2f)}
.about__photo{position:absolute;left:40px;top:21px;width:171px;height:115px;
  background:
    radial-gradient(ellipse 22px 30px at 16% 40%,rgba(90,60,45,.85),transparent 70%),
    radial-gradient(ellipse 22px 28px at 52% 35%,rgba(215,180,140,.9),transparent 70%),
    radial-gradient(ellipse 18px 24px at 78% 40%,rgba(160,120,95,.8),transparent 70%),
    radial-gradient(ellipse 40px 30px at 50% 80%,rgba(60,65,75,.7),transparent 70%),
    radial-gradient(ellipse 30px 25px at 20% 85%,rgba(235,235,238,.9),transparent 70%),
    linear-gradient(120deg,#d9dde2,#f3f4f6 40%,#b7c0ca 75%,#8a96a3)}
.about__body{position:absolute;left:222px;top:20px;width:190px;color:var(--white)}
.about__body h2{font-size:11px;font-weight:700;margin-bottom:4px}
.about__body p{font-size:5.4px;line-height:10.8px;margin-bottom:10px}
.pill{display:inline-block;height:15px;padding:0 9px;border-radius:8px;background:var(--teal);color:var(--white);font-size:5.4px;font-weight:600;line-height:15px;margin-right:5px}

/* features */
.features{position:absolute;left:0;top:603px;width:434px;height:175px;
  background:radial-gradient(ellipse 120px 90px at 42% 55%,rgba(225,215,205,.55),transparent 70%),linear-gradient(90deg,#e6e9ec,#f4f5f6 50%,#dfe4e8)}
.features h2{position:absolute;left:38px;top:43px;font-size:11px;font-weight:700;color:var(--blue-dark)}
.features ul{position:absolute;left:38px;top:62px;width:182px;list-style:none;font-size:5.5px;line-height:10.8px}
.features li{padding-left:8px;position:relative}
.features li::before{content:"»";position:absolute;left:0;font-weight:700}
.features .pill{position:absolute;left:38px;top:129px}
.features__accent{position:absolute;left:302px;top:24px;width:89px;height:125px;background:var(--blue)}
.features__photo{position:absolute;left:227px;top:31px;width:157px;height:111px;
  background:
    radial-gradient(ellipse 20px 26px at 60% 48%,rgba(120,80,60,.9),transparent 70%),
    radial-gradient(ellipse 30px 25px at 82% 70%,rgba(70,80,95,.95),transparent 70%),
    radial-gradient(ellipse 14px 6px at 84% 75%,rgba(240,150,60,.9),transparent 70%),
    radial-gradient(ellipse 30px 20px at 40% 15%,rgba(200,130,120,.6),transparent 70%),
    radial-gradient(ellipse 40px 25px at 30% 90%,rgba(40,40,45,.8),transparent 70%),
    linear-gradient(135deg,#7a6a5c,#b09a85 40%,#5d5a58 70%,#2f3237)}

/* footer */
.site-footer{position:absolute;left:0;width:434px;background:var(--blue);color:var(--white)}
.foot-col{position:absolute;top:27px}
.foot-col h4{font-size:6.8px;font-weight:500;margin-bottom:7px;white-space:nowrap}
.foot-col p{font-size:4.6px;line-height:7.8px;width:95px;opacity:.9}
.foot-col ul{list-style:none;font-size:5px;line-height:13.5px}
.foot-col--links li::before{content:"» "}
.newsletter input{display:block;width:106px;height:13px;border:0;font-family:inherit;font-size:5px;padding:0 6px;color:#777}
.newsletter .sub{display:inline-block;margin-top:6px;height:12px;padding:0 8px;background:var(--teal);font-size:5.6px;line-height:12px}
.newsletter .socials{display:flex;gap:4px;margin-top:6px}
.newsletter .socials i{display:block;width:13px;height:13px;border:1px solid var(--white);border-radius:50%}
.copyright{position:absolute;left:0;width:434px;height:25px;background:#2a8fcf;font-size:4.8px;color:var(--white);text-align:center;line-height:25px}
.copyright span{position:absolute;right:4px;font-size:4px}

/* contact page */
.page-banner{position:absolute;left:0;width:434px;text-align:center;color:var(--white);z-index:1}
.page-banner h1{font-size:13px;font-weight:700;line-height:14px}
.page-banner .crumbs{font-size:7.4px;margin:3px 0 8px}
.callback{display:inline-flex;align-items:center;gap:3px;height:17px;padding:0 9px;border-radius:9px;background:var(--blue);font-size:5.5px;font-weight:600;color:var(--white)}
.callback svg{width:6px;height:6px;fill:var(--white)}
.info-card{position:absolute;top:278px;width:111px;height:52px;border:1px solid #eceeef;text-align:center;padding-top:7px;box-shadow:0 1px 2px rgba(0,0,0,.04)}
.info-card h3{display:flex;justify-content:center;align-items:center;gap:3px;font-size:7.8px;font-weight:500;color:var(--blue);margin-bottom:2px}
.info-card svg{width:7px;height:7px;fill:var(--blue)}
.info-card p{font-size:5.5px;line-height:10px}
.contact-form{position:absolute;left:0;top:350px;width:434px;height:161px;background:var(--soft)}
.contact-form .field{position:absolute;width:147px;height:13px;margin:0;font-size:4.5px;padding:3px 5px}
.submit{position:absolute;left:186px;top:124px;width:62px;height:18px;border-radius:9px;background:var(--teal);color:var(--white);font-size:5.8px;font-weight:600;text-align:center;line-height:18px}
</style>
</head>
<body>

<main class="page page--home">
  <header class="site-header">
    <div class="brand"><span class="brand__dot"></span><span class="brand__name">Callwise</span></div>
    <div class="contact-strip">
      <span><svg viewBox="0 0 10 10"><path d="M0 4L10 0 6 10 5 5z"/></svg>PO Box 42, Marlow WA 6011, USA</span>
      <span><svg viewBox="0 0 10 10"><path d="M2 0l2 2.5-1 1.5a6 6 0 003 3l1.5-1L10 8l-1.5 2C4 10 0 6 0 1.5z"/></svg>Phone: 555 010 2030</span>
      <span><svg viewBox="0 0 10 10"><path d="M0 2h10v6H0zM0 2l5 3.5L10 2"/></svg>Email: info@callwise.example</span>
    </div>
    <nav class="main-nav">
      <span class="is-active">Home</span><span>About us</span><span>Services</span><span>Blog</span><span>Contact us</span>
      <span class="social-mini"><i></i><i></i><i></i></span>
      <svg viewBox="0 0 10 10" fill="none" stroke="#222" stroke-width="1.5"><circle cx="4" cy="4" r="3"/><path d="M6.3 6.3L9.5 9.5"/></svg>
    </nav>
  </header>

  <section class="hero" style="height:237px">
    <div class="hero__photo" role="img" aria-label="Smiling call centre agent wearing a headset in a busy office"></div>
    <form class="quote-box">
      <h2>GET A FREE QUOTE</h2>
      <p>Sed ut perspiciatis unde omnis iste natus<br>error sit voluptatem</p>
      <span class="field">First Name</span>
      <span class="field">Last Name</span>
      <span class="field">Email</span>
      <div class="field-row"><span class="field">Phone Number</span><span class="field field--select">Select Services</span></div>
      <span class="field field--area">Description</span>
      <span class="btn-quote">GET A QUOTE</span>
    </form>
    <svg class="hero__curve" viewBox="0 0 434 40" preserveAspectRatio="none">
      <path d="M0 40V31Q217 -2 434 31V40Z" fill="#fff"/>
      <path d="M48 23Q217 -3 386 23" fill="none" stroke="#1a78c8" stroke-width="2.4"/>
    </svg>
  </section>

  <h2 class="sec-title" style="top:302px">Our Services</h2>
  <p class="sec-lead" style="top:322px">Lorem ipsum dolor sit amet, consectetur adipiscing elit. Fusce aliquet, massa ac ornare feugiat, nunc dui auctor ipsum, sed posuere eros sapien id quam.</p>

  <article class="service" style="left:40px">
    <svg viewBox="0 0 20 20"><circle cx="10" cy="7" r="4"/><path d="M3 18c1-4 4-6 7-6s6 2 7 6"/><path d="M5 8a5 5 0 0110 0"/></svg>
    <h3>TORMALUX SUPPORT</h3>
    <p>Lorem ipsum dolor sit amet, consectetur adipiscing elit. Fusce aliquet, massa ac ornare.</p>
  </article>
  <article class="service service--featured" style="left:162px">
    <svg viewBox="0 0 20 20"><rect x="1" y="1" width="6" height="5"/><rect x="13" y="1" width="6" height="5"/><rect x="7" y="14" width="6" height="5"/><path d="M4 6v4h12V6M10 10v4"/></svg>
    <h3>TORMALUX HOSTING</h3>
    <p>Lorem ipsum dolor sit amet, consectetur adipiscing elit. Fusce aliquet, massa ac ornare.</p>
  </article>
  <article class="service" style="left:282px">
    <svg viewBox="0 0 20 20"><rect x="4" y="2" width="12" height="17"/><path d="M8 1h4v3H8zM7 8h2M11 8h2M7 12h2M11 12h2M7 16h2"/></svg>
    <h3>TORMALUX CUSTOMISATION</h3>
    <p>Lorem ipsum dolor sit amet, consectetur adipiscing elit. Fusce aliquet, massa ac ornare.</p>
  </article>

  <section class="about">
    <div class="about__photo" role="img" aria-label="Team of call centre agents with headsets at their desks"></div>
    <div class="about__body">
      <h2>ABOUT US</h2>
      <p>Sed ut perspiciatis unde omnis iste natus error sit voluptatem accusantium doloremque laudantium, totam rem aperiam, eaque ipsa quae ab illo inventore veritatis et quasi architecto beatae vitae dicta sunt explicabo.</p>
      <p>Sed ut perspiciatis unde omnis iste natus error sit voluptatem accusantium doloremque laudantium, totam rem aperiam.</p>
      <span class="pill">Read More</span><span class="pill">Contact us</span>
    </div>
  </section>

  <section class="features">
    <h2>KEY SELLING FEATURES</h2>
    <ul>
      <li>Australian based</li>
      <li>PCI complaint</li>
      <li>10+ years of dialler and call centre experience</li>
      <li>we run a sister company which is a highly reputable 40 seat call centre, so we know first hand about call centre technology.</li>
    </ul>
    <span class="pill" style="top:135px">Read More</span>
    <div class="features__accent"></div>
    <div class="features__photo" role="img" aria-label="Agent working at a dialler dashboard in a call centre"></div>
  </section>

  <footer class="site-footer" style="top:778px;height:115px">
    <div class="foot-col" style="left:34px"><h4>ABOUT COMPANY</h4><p>Sed ut perspiciatis unde omnis iste natus error sit voluptatem accusantium doloremque laudantium, totam rem aperiam, eaque ipsa quae illo inventore veritatis et quasi architecto beatae vitae dicta sunt explicabo.</p></div>
    <div class="foot-col foot-col--links" style="left:150px"><h4>QUICK LINKS</h4><ul><li>Home</li><li>About Us</li><li>Services</li><li>Key selling</li></ul></div>
    <div class="foot-col foot-col--links" style="left:224px"><h4>OTHER LINKS</h4><ul><li>Privacy Policy</li><li>Terms of Use</li><li>Contact Us</li></ul></div>
    <div class="foot-col newsletter" style="left:288px"><h4>SIGN UP NEWSLETTER</h4><input value="Email address" readonly><span class="sub">Subscribe</span><div class="socials"><i></i><i></i><i></i><i></i></div></div>
  </footer>
  <div class="copyright" style="top:893px">© 2018 Company Name. All right reserved<span>C29</span></div>
</main>

<main class="page page--contact">
  <header class="site-header">
    <div class="brand"><span class="brand__dot"></span><span class="brand__name">Callwise</span></div>
    <div class="contact-strip">
      <span><svg viewBox="0 0 10 10"><path d="M0 4L10 0 6 10 5 5z"/></svg>PO Box 42, Marlow WA 6011, USA</span>
      <span><svg viewBox="0 0 10 10"><path d="M2 0l2 2.5-1 1.5a6 6 0 003 3l1.5-1L10 8l-1.5 2C4 10 0 6 0 1.5z"/></svg>Phone: 555 010 2030</span>
      <span><svg viewBox="0 0 10 10"><path d="M0 2h10v6H0zM0 2l5 3.5L10 2"/></svg>Email: info@callwise.example</span>
    </div>
    <nav class="main-nav">
      <span>Home</span><span>About us</span><span>Services</span><span>Blog</span><span class="is-active">Contact us</span>
      <span class="social-mini"><i></i><i></i><i></i></span>
      <svg viewBox="0 0 10 10" fill="none" stroke="#222" stroke-width="1.5"><circle cx="4" cy="4" r="3"/><path d="M6.3 6.3L9.5 9.5"/></svg>
    </nav>
  </header>

  <section class="hero" style="height:165px">
    <div class="hero__photo hero__photo--dim" role="img" aria-label="Call centre agents with headsets, softly darkened behind the page title"></div>
    <svg class="hero__curve" viewBox="0 0 434 40" preserveAspectRatio="none">
      <path d="M0 40V31Q217 -2 434 31V40Z" fill="#fff"/>
      <path d="M48 23Q217 -3 386 23" fill="none" stroke="#1a78c8" stroke-width="2.4"/>
    </svg>
  </section>
  <div class="page-banner" style="top:88px">
    <h1>CONTACT US</h1>
    <div class="crumbs">Home &gt; Contact us</div>
    <span class="callback"><svg viewBox="0 0 10 10"><path d="M2 0l2 2.5-1 1.5a6 6 0 003 3l1.5-1L10 8l-1.5 2C4 10 0 6 0 1.5z"/></svg>REQUEST CALL BACK</span>
  </div>

  <h2 class="sec-title" style="top:231px">Get in touch</h2>
  <p class="sec-lead" style="top:251px">Lorem ipsum dolor sit amet, consectetur adipiscing elit. Fusce aliquet, massa ac ornare feugiat, nunc dui auctor ipsum, sed posuere eros sapien id quam.</p>

  <div class="info-card" style="left:40px"><h3><svg viewBox="0 0 10 10"><path d="M5 0a3.5 3.5 0 013.5 3.5C8.5 6 5 10 5 10S1.5 6 1.5 3.5A3.5 3.5 0 015 0zm0 2a1.5 1.5 0 100 3 1.5 1.5 0 000-3z"/></svg>Address</h3><p>PO Box 42, Marlow<br>WA 6011, USA</p></div>
  <div class="info-card" style="left:161px"><h3><svg viewBox="0 0 10 10"><path d="M0 2h10v1L5 6 0 3zM0 4l5 3 5-3v4H0z"/></svg>E-Mail</h3><p>info@callwise.example<br>help@callwise.example</p></div>
  <div class="info-card" style="left:282px"><h3><svg viewBox="0 0 10 10"><path d="M2 0l2 2.5-1 1.5a6 6 0 003 3l1.5-1L10 8l-1.5 2C4 10 0 6 0 1.5z"/></svg>Phone</h3><p>555 010 2030<br>555 010 2031</p></div>

  <form class="contact-form">
    <h2 class="sec-title" style="top:17px">Get a free quote</h2>
    <span class="field" style="left:66px;top:42px">Name</span>
    <span class="field" style="left:221px;top:42px">Email</span>
    <span class="field" style="left:66px;top:61px">Phone Number</span>
    <span class="field" style="left:221px;top:61px;height:51px">Message :</span>
    <span class="field" style="left:66px;top:80px">Address</span>
    <span class="field" style="left:66px;top:99px">Zipcode</span>
    <span class="submit">SUBMIT NOW</span>
  </form>

  <footer class="site-footer" style="top:511px;height:115px">
    <div class="foot-col" style="left:34px"><h4>ABOUT COMPANY</h4><p>Sed ut perspiciatis unde omnis iste natus error sit voluptatem accusantium doloremque laudantium, totam rem aperiam, eaque ipsa quae illo inventore veritatis et quasi architecto beatae vitae dicta sunt explicabo.</p></div>
    <div class="foot-col foot-col--links" style="left:150px"><h4>QUICK LINKS</h4><ul><li>Home</li><li>About Us</li><li>Services</li><li>Key selling</li></ul></div>
    <div class="foot-col" style="left:223px"><h4>OTHER LINKS</h4><ul><li>Privacy Policy</li><li>Terms of Use</li><li>Contact Us</li></ul></div>
    <div class="foot-col newsletter" style="left:287px"><h4>SIGN UP NEWSLETTER</h4><input value="Email address" readonly><span class="sub">Subscribe</span><div class="socials"><i></i><i></i><i></i><i></i></div></div>
  </footer>
  <div class="copyright" style="top:626px">© 2018 Company Name. All right reserved<span>C29</span></div>
</main>

</body>
</html>
```